Road Construction Company needs business cards

We would like a new business card designed for our business.

We're a road construction company based in Qld, Australia.

Can the business card please have the following information on it.

Name: Warren Halbeck
Position: General Manager
Phone: 0472 915 348
Email: Warren.halbeck@tovrin.com.au
Address: 87 Marrow Ave, Pendlebay, QLD, 4023
Website: www.tovrin.com.au

Visually we'd like the card to be professional and simple.

Attached is our logo.

Our website is www.tovrin.com.au

Target Market(s)

Men aged 25-60

Contact Information for Business Card

As listed in project description

Font styles to use
Serif

Requirements
Must have
• Large logo on back of card

```html
<!DOCTYPE html>
<html lang="en">
<head>
<meta charset="utf-8">
<title>Tovrin Business Card</title>
<link href="https://fonts.googleapis.com/css2?family=Fira+Sans:wght@400;600;800&display=swap" rel="stylesheet">
<style>
  :root {
    --backdrop: #8e9194;
    --card-white: #ffffff;
    --brand-blue: #0553a5;
    --accent-blue: #3aa0dc;
    --text-white: #ffffff;
  }
  html, body {
    margin: 0;
    padding: 0;
    width: 1200px;
    height: 1200px;
    overflow: hidden;
    background: var(--backdrop);
    font-family: "Fira Sans", sans-serif;
  }
  .card {
    position: absolute;
    width: 636px;
    height: 404px;
    box-sizing: border-box;
  }
  .card-front {
    left: 156px;
    top: 151px;
    background: var(--card-white);
    display: flex;
    align-items: center;
    justify-content: center;
  }
  .brand-name {
    margin: 0 0 10px 0;
    font-family: "Fira Sans", sans-serif;
    font-weight: 800;
    font-size: 56px;
    letter-spacing: 3px;
    color: var(--brand-blue);
    line-height: 1;
  }
  .card-back {
    left: 373px;
    top: 672px;
    background: var(--brand-blue);
    color: var(--text-white);
    text-align: center;
  }
  .person-name {
    position: absolute;
    top: 90px;
    left: 0;
    right: 0;
    margin: 0;
    font-weight: 600;
    font-size: 24px;
    letter-spacing: 0.3px;
  }
  .person-role {
    position: absolute;
    top: 120px;
    left: 0;
    right: 0;
    margin: 0;
    font-weight: 400;
    font-size: 19px;
    color: var(--accent-blue);
  }
  .icon-rail {
    position: absolute;
    left: 153px;
    top: 160px;
  }
  .contact-list {
    position: absolute;
    top: 206px;
    left: 0;
    right: 0;
    margin: 0;
    padding: 0;
    list-style: none;
    font-size: 15.5px;
    line-height: 27.7px;
  }
</style>
</head>
<body>
  <section class="card card-front">
    <h1 class="brand-name">TOVRIN</h1>
  </section>

  <section class="card card-back">
    <h2 class="person-name">WARREN HALBECK</h2>
    <p class="person-role">General Manager</p>

    <svg class="icon-rail" width="328" height="34" viewBox="0 0 328 34" aria-hidden="true">
      <g stroke="#ffffff" stroke-width="1.6" fill="none">
        <line x1="0" y1="17" x2="77" y2="17"/>
        <line x1="109" y1="17" x2="123" y2="17"/>
        <line x1="155" y1="17" x2="170" y2="17"/>
        <line x1="202" y1="17" x2="217" y2="17"/>
        <line x1="249" y1="17" x2="328" y2="17"/>
        <circle cx="93" cy="17" r="16"/>
        <circle cx="139" cy="17" r="16"/>
        <circle cx="186" cy="17" r="16"/>
        <circle cx="233" cy="17" r="16"/>
      </g>
      <g fill="#3aa0dc">
        <!-- phone -->
        <path d="M85 16 q8 -6 16 0 l0 2 -3 1 -1 -2 q-4 -1.5 -8 0 l-1 2 -3 -1 z"/>
        <rect x="88" y="19" width="10" height="4" rx="1"/>
        <!-- envelope -->
        <rect x="132" y="12" width="14" height="10" rx="1"/>
        <path d="M132.5 12.5 L139 18 L145.5 12.5" stroke="#0553a5" stroke-width="1.2" fill="none"/>
        <!-- pin -->
        <path d="M233 9 a5.5 5.5 0 0 1 5.5 5.5 c0 4 -5.5 10 -5.5 10 c0 0 -5.5 -6 -5.5 -10 a5.5 5.5 0 0 1 5.5 -5.5 z"/>
        <circle cx="233" cy="14.5" r="2" fill="#0553a5"/>
      </g>
      <!-- globe -->
      <g stroke="#3aa0dc" stroke-width="1.3" fill="none">
        <circle cx="186" cy="17" r="7"/>
        <ellipse cx="186" cy="17" rx="3" ry="7"/>
        <line x1="179" y1="17" x2="193" y2="17"/>
      </g>
    </svg>

    <ul class="contact-list">
      <li>0472 915 348</li>
      <li>Warren.halbeck@tovrin.com.au</li>
      <li>www.tovrin.com.au</li>
      <li>87 Marrow Ave, Pendlebay, QLD, 4023</li>
    </ul>
  </section>
</body>
</html>
```